Manufacturer Website with Home and Product page

We have this website, veltaro.com, but we need another one for the Canadian market. Canadians like to deal with Canadians so we need to gear it to that. It will be a simpler website than the current site.

We will need a design for two pages, one for the home page and one for a product page.

I synthesized all the brief information for the designers here, descriptions for both pages are included:

https://files.brimlodge.net/doc/8qwx3Lm2Rt7Yp0KzVb4Nc6HsJd9FgA1eUi5Tr

Supporting Folder:
https://files.brimlodge.net/folder/7ZpqW3nTx8Kd2LmR5vYb0HcJs

Industry/Entity Type

Tanning Beds, Red Light Beds, Hydro massage beds

Number of Pages Required

2 page

Requirements
Must have
• Two page descriptions: https://files.brimlodge.net/doc/8qwx3Lm2Rt7Yp0KzVb4Nc6HsJd9FgA1eUi5Tr/view
Nice to have
• Information Folder: https://files.brimlodge.net/folder/u/0/7ZpqW3nTx8Kd2LmR5vYb0HcJs

```html
<!DOCTYPE html>
<html lang="en">
<head>
<meta charset="utf-8">
<title>Veltaro Canada — Commercial Tanning, Red Light and Water Massage</title>
<link rel="stylesheet" href="https://fonts.googleapis.com/css2?family=DM+Serif+Display&family=Playfair+Display:ital,wght@1,600&family=Poppins:wght@400;500;600&display=swap">
<style>
:root{
  --purple:#6f7cc4;
  --purple-dark:#5a67b3;
  --red:#e2493d;
  --ink:#1d1d1f;
  --text:#4a4a4a;
  --grey-bg:#f1f1f4;
  --white:#fff;
  --bar:#2b2b2e;
}
*{margin:0;padding:0;box-sizing:border-box}
html,body{width:1200px;height:4121px;overflow:hidden}
body{position:relative;background:var(--white);font-family:"Poppins",sans-serif;color:var(--text)}
.abs{position:absolute}
.serif{font-family:"DM Serif Display",serif;color:var(--ink);font-weight:400}
a{color:inherit;text-decoration:none}

/* header */
.site-header{position:absolute;left:0;top:0;width:1200px;height:96px;background:var(--white);z-index:5;box-shadow:0 1px 0 #eee}
.brand{position:absolute;left:163px;top:20px;font-family:"DM Serif Display",serif;font-size:44px;color:var(--purple);line-height:1}
.brand-sub{position:absolute;left:198px;top:62px;font-size:9px;letter-spacing:8px;color:var(--purple)}
.call{position:absolute;left:708px;top:14px;display:flex;align-items:center;gap:10px}
.call-icon{width:32px;height:32px;border:1px solid #f1c5c1;border-radius:50%;display:flex;align-items:center;justify-content:center}
.call small{display:block;font-size:11px;color:var(--ink)}
.call strong{display:block;font-size:16px;font-weight:600;color:var(--ink);line-height:1.1}
.divider{position:absolute;left:870px;top:16px;width:1px;height:30px;background:#ddd}
.btn-catalog{position:absolute;left:888px;top:14px;width:148px;height:34px;border-radius:17px;background:var(--red);color:#fff;font-size:12px;display:flex;align-items:center;justify-content:center}
.nav{position:absolute;top:64px;left:0;font-size:12px;color:#333}
.nav span{position:absolute;white-space:nowrap}
.nav .active{color:var(--red)}
.nav .active::after{content:"";position:absolute;left:-4px;right:-4px;top:22px;height:2px;background:var(--red)}

/* hero */
.hero-photo{position:absolute;left:0;top:96px;width:1200px;height:560px;
  background:
    radial-gradient(ellipse 420px 260px at 1010px 170px, rgba(70,105,205,.95), rgba(70,105,205,0) 70%),
    radial-gradient(ellipse 380px 200px at 760px 130px, rgba(190,210,245,.9), rgba(190,210,245,0) 70%),
    radial-gradient(ellipse 300px 200px at 160px 220px, rgba(240,220,220,.55), rgba(240,220,220,0) 70%),
    linear-gradient(100deg,#f7f8fb 0%,#eef2fa 40%,#c9d7f2 62%,#6f8fd6 85%,#4a66c2 100%);
  clip-path:path("M0,0 H1200 V374 C900,494 520,544 0,424 Z")}
.hero-product{position:absolute;left:780px;top:430px;width:340px;height:240px;z-index:2;
  background:
    radial-gradient(ellipse 150px 40px at 170px 210px, rgba(150,220,140,.75), rgba(150,220,140,0) 70%),
    radial-gradient(ellipse 130px 70px at 230px 60px, rgba(110,140,215,.7), rgba(110,140,215,0) 70%),
    radial-gradient(ellipse 170px 120px at 150px 140px, #fafbfc 0%, #e4e7ec 55%, rgba(210,214,222,0) 100%);
  border-radius:50%;filter:blur(1px)}
.hero-title{position:absolute;left:165px;top:190px;font-family:"Playfair Display",serif;font-style:italic;font-weight:600;font-size:30px;line-height:43px;color:var(--ink);z-index:3}
.btn-red{position:absolute;left:163px;top:379px;width:162px;height:40px;border-radius:20px;background:var(--red);color:#fff;font-size:12px;display:flex;align-items:center;justify-content:center;z-index:3}
.scroll-down{position:absolute;left:188px;top:521px;width:78px;height:78px;border-radius:50%;background:rgba(255,255,255,.9);display:flex;align-items:center;justify-content:center;z-index:4;box-shadow:0 4px 14px rgba(0,0,0,.12)}
.scroll-down div{width:60px;height:60px;border-radius:50%;background:var(--purple);display:flex;align-items:center;justify-content:center}

/* products */
.section-title{position:absolute;left:0;width:1200px;text-align:center;font-size:38px}
.ph{position:absolute}
.overlay-box{position:absolute;left:152px;top:856px;width:400px;height:371px;background:rgba(111,124,196,.88);color:#fff;text-align:center;padding:0 34px}
.overlay-box h3{font-family:"DM Serif Display",serif;font-weight:400;font-size:30px;margin-top:86px}
.overlay-box p{font-size:12px;line-height:23px;margin-top:14px;opacity:.92}
.overlay-box a{display:inline-block;margin-top:14px;font-size:12px;text-decoration:underline}
.tile-label{position:absolute;font-family:"DM Serif Display",serif;font-size:30px;color:#fff;text-shadow:0 1px 6px rgba(0,0,0,.3)}

/* industries */
.industries{position:absolute;left:0;top:1355px;width:1200px;height:1168px;background:var(--grey-bg)}
.card{position:absolute;width:226px;height:438px;background:var(--white);text-align:center}
.card .photo{height:219px;width:100%}
.card .badge{position:absolute;left:74px;top:180px;width:78px;height:78px;border-radius:50%;background:var(--purple);border:3px solid #fff;display:flex;align-items:center;justify-content:center}
.card h4{margin-top:52px;font-weight:500;font-size:17px;color:var(--ink)}
.card p{font-size:12px;line-height:20px;padding:0 14px;margin-top:8px;color:#555;height:80px;overflow:hidden}
.card a{display:block;margin-top:8px;font-size:12px;color:var(--purple);text-decoration:underline}

/* specialist */
.specialist{position:absolute;left:0;top:2523px;width:1200px;height:413px;
  background:
    radial-gradient(ellipse 220px 260px at 520px 260px, rgba(150,120,80,.35), rgba(150,120,80,0) 70%),
    radial-gradient(ellipse 200px 300px at 80px 200px, rgba(120,120,120,.35), rgba(120,120,120,0) 70%),
    radial-gradient(ellipse 260px 200px at 900px 300px, rgba(120,100,70,.3), rgba(120,100,70,0) 70%),
    linear-gradient(100deg,#2f3033 0%,#45433f 45%,#38362f 100%);
  text-align:center;color:#fff}
.specialist h2{font-family:"DM Serif Display",serif;font-weight:400;font-size:38px;color:#fff;margin-top:110px}
.specialist p{font-size:15px;line-height:26px;margin-top:12px}
.btn-purple{display:inline-flex;align-items:center;justify-content:center;background:var(--purple);color:#fff;font-size:13px;font-weight:500}
.specialist .btn-purple{width:276px;height:51px;margin-top:24px}

/* salon */
.salon-title{position:absolute;left:112px;top:3012px;font-size:40px}
.salon-sub{position:absolute;left:112px;top:3070px;font-size:14px;font-weight:500;color:var(--ink)}
.step{position:absolute;left:112px;display:flex;align-items:center;gap:20px;font-size:16px;color:var(--ink)}
.step svg{width:44px;height:44px}
.salon .btn-purple{position:absolute;left:112px;top:3365px;width:158px;height:51px}
.salon-accent{position:absolute;left:622px;top:3042px;width:472px;height:383px;background:var(--purple)}

/* footer */
.footer{position:absolute;left:0;top:3517px;width:1200px;height:555px;
  background:
    linear-gradient(180deg,rgba(127,136,203,0) 60%,rgba(95,104,175,.55) 100%),
    linear-gradient(180deg,#7f88cb 0%,#7a84c6 60%,#6d77bc 100%);color:#fff}
.footer .brand{color:#fff;left:112px;top:66px;font-size:56px}
.footer .brand-sub{color:#fff;left:156px;top:122px}
.f-contact{position:absolute;left:112px;font-size:12px;line-height:19px;display:flex;gap:12px}
.f-contact b{font-weight:600}
.f-head{position:absolute;top:72px;font-family:"DM Serif Display",serif;font-size:17px}
.f-links{position:absolute;top:104px;font-size:12px;line-height:31.5px}
.socials{position:absolute;left:827px;top:125px;display:flex;gap:9px}
.socials span{width:36px;height:36px;border:1.5px solid #fff;border-radius:50%}
.search{position:absolute;left:827px;top:177px;width:261px;height:45px;background:#fff;color:#555;font-size:11px;padding:0 14px;display:flex;align-items:center;justify-content:space-between}
.disclaimer{position:absolute;left:112px;top:410px;width:980px;font-size:10.5px;line-height:20px;color:#eef0fa}
.copyright{position:absolute;left:0;top:4072px;width:1200px;height:49px;background:var(--bar);color:#ddd;font-size:12px;display:flex;align-items:center;justify-content:center}
</style>
</head>
<body>

<header class="site-header">
  <div class="brand">Veltaro</div>
  <div class="brand-sub">CANADA</div>
  <div class="call">
    <span class="call-icon"><svg width="16" height="16" viewBox="0 0 24 24"><path d="M6.6 10.8a15 15 0 0 0 6.6 6.6l2.2-2.2a1 1 0 0 1 1-.25 11.4 11.4 0 0 0 3.6.6 1 1 0 0 1 1 1V20a1 1 0 0 1-1 1A17 17 0 0 1 3 4a1 1 0 0 1 1-1h3.5a1 1 0 0 1 1 1c0 1.25.2 2.45.6 3.6a1 1 0 0 1-.25 1z" fill="none" stroke="#e2493d" stroke-width="1.6"/></svg></span>
    <div><small>Call Us</small><strong>416 555 0192</strong></div>
  </div>
  <div class="divider"></div>
  <a class="btn-catalog">Request a Catalog</a>
  <nav class="nav">
    <span class="active" style="left:480px">Home</span>
    <span style="left:542px">Tanning ⌄</span>
    <span style="left:618px">Massage ⌄</span>
    <span style="left:699px">Red Light ⌄</span>
    <span style="left:782px">Salon Startup</span>
    <span style="left:890px">About Us</span>
    <span style="left:970px">Contact Us</span>
  </nav>
</header>

<section class="hero">
  <div class="hero-photo" role="img" aria-label="Photo of a client relaxing in a lit commercial tanning bed"></div>
  <svg class="abs" style="left:0;top:96px" width="1200" height="560" viewBox="0 96 1200 560">
    <path d="M0,520 C420,630 880,600 1200,470 V520 C900,640 430,660 0,532 Z" fill="#6f7cc4"/>
  </svg>
  <div class="hero-product" role="img" aria-label="Product photo of a white tanning bed with green accent lighting, lid open"></div>
  <h1 class="hero-title">“ The Leading Manufacturer<br>In Commercial Tanning, Red<br>Light And Water Massage<br>Therapy ”</h1>
  <a class="btn-red">View Our Products</a>
  <div class="scroll-down"><div><svg width="26" height="26" viewBox="0 0 24 24"><path d="M12 4v15M6 13l6 6 6-6" fill="none" stroke="#fff" stroke-width="2"/></svg></div></div>
</section>

<section class="products">
  <h2 class="section-title serif" style="top:742px">Our Products</h2>
  <div class="ph" role="img" aria-label="Photo of a tanning bed with glowing blue lamps" style="left:112px;top:819px;width:480px;height:447px;background:radial-gradient(ellipse 200px 120px at 120px 40px,#eef4fc,rgba(238,244,252,0) 70%),radial-gradient(ellipse 180px 200px at 430px 330px,#c8daf4,rgba(200,218,244,0) 70%),linear-gradient(135deg,#dce8f7,#7e9fdd 50%,#3f63b8)"></div>
  <div class="overlay-box">
    <h3>Tanning Beds</h3>
    <p>Lorem ipsum dolor sit amet consectetuer adipiscing elit, sed diam nonummy nibh euismod tincidunt ut laoreet dolore magna aliquam erat volutpat. Ut wisi enim ad minim quis nostrud exerci tation ullamcorper suscipit lobortis nisl ut aliquip ex ea.</p>
    <a>Read More</a>
  </div>
  <div class="ph" role="img" aria-label="Photo of a client stepping into a hydro massage bed" style="left:608px;top:819px;width:480px;height:215px;background:radial-gradient(ellipse 120px 150px at 280px 90px,rgba(110,80,150,.55),rgba(110,80,150,0) 70%),radial-gradient(ellipse 200px 80px at 120px 110px,#f2f3f4,rgba(242,243,244,0) 70%),linear-gradient(90deg,#b9c3c4,#8a9597 45%,#aab8b6 75%,#6c7a7a),linear-gradient(180deg,transparent 60%,#2b2d30)"></div>
  <div class="ph" style="left:608px;top:819px;width:480px;height:215px;background:linear-gradient(180deg,rgba(0,0,0,0) 50%,rgba(20,22,25,.6))"></div>
  <div class="tile-label" style="left:626px;top:975px">Hydro Massage</div>
  <div class="ph" role="img" aria-label="Photo of a client resting under a red light therapy bed" style="left:608px;top:1051px;width:480px;height:215px;background:radial-gradient(ellipse 120px 90px at 420px 60px,#ff6a55,rgba(255,106,85,0) 70%),radial-gradient(ellipse 200px 70px at 380px 160px,#f7e6e0,rgba(247,230,224,0) 70%),radial-gradient(ellipse 200px 90px at 120px 110px,#d8322a,rgba(216,50,42,0) 70%),linear-gradient(135deg,#f4d2cb,#e7695e 45%,#c3332b)"></div>
  <div class="tile-label" style="left:626px;top:1207px">Red Light Beds</div>
</section>

<section class="industries">
  <h2 class="section-title serif" style="top:80px">Endless Industry Applications</h2>
</section>

<div class="card" style="left:112px;top:1520px">
  <div class="photo" role="img" aria-label="Photo of residents chatting in a shared lounge" style="background:radial-gradient(ellipse 80px 60px at 150px 160px,#3d4046,rgba(61,64,70,0) 70%),radial-gradient(ellipse 90px 80px at 60px 50px,#f1ede5,rgba(241,237,229,0) 70%),linear-gradient(160deg,#dcd7cd,#a19b90 55%,#5e5a54)"></div>
  <div class="badge"><svg width="36" height="36" viewBox="0 0 24 24" fill="none" stroke="#fff" stroke-width="1.3"><path d="M3 11l9-7 9 7M5 10v10h14V10M10 20v-5h4v5"/></svg></div>
  <h4>Housing</h4>
  <p>Distinguish your community by providing a comprehensive range of amenities to your residents.</p>
  <a>Read More</a>
</div>
<div class="card" style="left:362px;top:1520px">
  <div class="photo" role="img" aria-label="Photo of medical staff reviewing scans" style="background:radial-gradient(ellipse 90px 40px at 120px 30px,#e7eef6,rgba(231,238,246,0) 70%),radial-gradient(ellipse 70px 100px at 60px 170px,#23324a,rgba(35,50,74,0) 70%),radial-gradient(ellipse 60px 100px at 180px 160px,#e9e9ec,rgba(233,233,236,0) 70%),linear-gradient(160deg,#a7b9cf,#4d5f78 60%,#25303f)"></div>
  <div class="badge"><svg width="36" height="36" viewBox="0 0 24 24" fill="none" stroke="#fff" stroke-width="1.3"><path d="M4 13h4l2-4 3 7 2-3h5M12 21s-8-5-8-11a4 4 0 0 1 8-1 4 4 0 0 1 8 1"/></svg></div>
  <h4>Medical</h4>
  <p>Veltaro offers a diverse range of wellness equipment specifically designed for medical facilities, enabling</p>
  <a>Read More</a>
</div>
<div class="card" style="left:611px;top:1520px">
  <div class="photo" role="img" aria-label="Photo of a fitness class in a brick studio" style="background:radial-gradient(ellipse 100px 60px at 113px 40px,#e9e1d8,rgba(233,225,216,0) 70%),radial-gradient(ellipse 100px 90px at 113px 170px,#2b2b30,rgba(43,43,48,0) 70%),linear-gradient(90deg,#8c5b47,#c9a58e 30%,#b88c74 70%,#7a4e3e)"></div>
  <div class="badge"><svg width="36" height="36" viewBox="0 0 24 24" fill="none" stroke="#fff" stroke-width="1.3"><path d="M12 20s-8-5-8-11a4 4 0 0 1 8-1 4 4 0 0 1 8 1c0 6-8 11-8 11zM6 12h3l2-3 2 5 1-2h4"/></svg></div>
  <h4>Fitness</h4>
  <p>Veltaro's cutting-edge equipment empowers fitness enthusiasts to elevate their training routine to new heights.</p>
  <a>Read More</a>
</div>
<div class="card" style="left:861px;top:1520px">
  <div class="photo" role="img" aria-label="Photo of a spa guest relaxing in a towel" style="background:radial-gradient(ellipse 90px 80px at 110px 150px,#fbfaf8,rgba(251,250,248,0) 70%),radial-gradient(ellipse 60px 60px at 30px 40px,#f4f2ee,rgba(244,242,238,0) 70%),linear-gradient(160deg,#ede2d4,#c6ae94 55%,#8e7660)"></div>
  <div class="badge"><svg width="36" height="36" viewBox="0 0 24 24" fill="none" stroke="#fff" stroke-width="1.3"><circle cx="12" cy="9" r="4"/><path d="M4 20c1-4 4-6 8-6s7 2 8 6"/></svg></div>
  <h4>Beauty/Spa</h4>
  <p>Distinguish yourself as a premier industry leader in your region by providing an array of our exquisite luxury wellness</p>
  <a>Read More</a>
</div>
<div class="card" style="left:237px;top:1992px">
  <div class="photo" role="img" aria-label="Photo of friends in sunglasses at the beach" style="background:radial-gradient(ellipse 70px 60px at 60px 40px,#f2e2b8,rgba(242,226,184,0) 70%),radial-gradient(ellipse 70px 60px at 170px 50px,#e8cfa0,rgba(232,207,160,0) 70%),radial-gradient(ellipse 120px 60px at 113px 130px,#e9b99a,rgba(233,185,154,0) 70%),linear-gradient(180deg,#f3dbb0,#e2b48c 55%,#3b86c6)"></div>
  <div class="badge"><svg width="36" height="36" viewBox="0 0 24 24" fill="none" stroke="#fff" stroke-width="1.3"><circle cx="12" cy="9" r="4"/><path d="M4 17h16M5 20h14"/></svg></div>
  <h4>Tanning</h4>
  <p>Whether you're embarking on a new salon venture or seeking to upgrade your existing equipment, Veltaro offers</p>
  <a>Read More</a>
</div>
<div class="card" style="left:486px;top:1992px">
  <div class="photo" role="img" aria-label="Photo of a resort pool seen from above" style="background:radial-gradient(ellipse 80px 40px at 150px 20px,#2f6f86,rgba(47,111,134,0) 70%),radial-gradient(ellipse 110px 50px at 90px 100px,#7fe0cf,rgba(127,224,207,0) 70%),linear-gradient(170deg,#6f9aa6,#58c7b4 40%,#cfd6d0 75%,#9aa49e)"></div>
  <div class="badge"><svg width="36" height="36" viewBox="0 0 24 24" fill="none" stroke="#fff" stroke-width="1.3"><rect x="5" y="5" width="14" height="14" rx="2"/><path d="M9 12h6M12 9v6"/></svg></div>
  <h4>Hospitality</h4>
  <p>The days of relying solely on room rentals for revenue are behind us. Elevate your guests' experience by providing</p>
  <a>Read More</a>
</div>
<div class="card" style="left:736px;top:1992px">
  <div class="photo" role="img" aria-label="Photo of colleagues silhouetted against an office window" style="background:radial-gradient(ellipse 130px 50px at 113px 130px,#1a1a1a,rgba(26,26,26,0) 70%),linear-gradient(180deg,#f6f6f6 0%,#d8d8d8 45%,#6d6d6d 70%,#2a2a2a)"></div>
  <div class="badge"><svg width="36" height="36" viewBox="0 0 24 24" fill="none" stroke="#fff" stroke-width="1.3"><path d="M12 18c-3-2-4-6 0-11 4 5 3 9 0 11zM12 18c-4 0-7-2-8-6 4 0 7 2 8 6zM12 18c4 0 7-2 8-6-4 0-7 2-8 6z"/></svg></div>
  <h4>Corporate Wellness</h4>
  <p>Elevate your corporate wellness center and stand out from the competition by providing a comprehensive</p>
  <a>Read More</a>
</div>

<section class="specialist" role="img" aria-label="Background photo of a sales office, darkened">
  <h2>Speak To a Specialist</h2>
  <p>Questions about products, pricing, or availability?<br>Speak to a Veltaro sales specialist now and get the answers you're looking for.</p>
  <a class="btn-purple">SPEAK TO A SPECIALIST NOW</a>
</section>

<section class="salon">
  <h2 class="salon-title serif">Starting a Salon or Spa?</h2>
  <p class="salon-sub">We've done it 100s of Times and Will Help You</p>
  <div class="step" style="top:3109px"><svg viewBox="0 0 44 44" fill="none" stroke="#6f7cc4" stroke-width="1.4"><rect x="4" y="8" width="30" height="26"/><path d="M10 28l6-7 5 4 8-9"/><circle cx="34" cy="30" r="6"/></svg>Develop a Business Plan</div>
  <div class="step" style="top:3173px"><svg viewBox="0 0 44 44" fill="none" stroke="#6f7cc4" stroke-width="1.4"><circle cx="22" cy="22" r="12"/><ellipse cx="22" cy="22" rx="20" ry="6"/></svg>Space Design</div>
  <div class="step" style="top:3242px"><svg viewBox="0 0 44 44" fill="none" stroke="#6f7cc4" stroke-width="1.4"><circle cx="22" cy="12" r="6"/><path d="M8 36V26h28v10M14 26v10M22 26v10M30 26v10"/></svg>Review Financing Options</div>
  <div class="step" style="top:3300px"><svg viewBox="0 0 44 44" fill="none" stroke="#6f7cc4" stroke-width="1.4"><rect x="6" y="14" width="20" height="16"/><path d="M26 18l10-6v20l-10-6M12 30v6"/></svg>Starup Marketing</div>
  <a class="btn-purple">LEARN MORE</a>
  <div class="salon-accent"></div>
  <div class="ph" role="img" aria-label="Photo of a spa receptionist greeting a client in a robe" style="left:606px;top:3026px;width:482px;height:393px;background:radial-gradient(ellipse 120px 130px at 340px 160px,#a07a4e,rgba(160,122,78,0) 70%),radial-gradient(ellipse 90px 160px at 120px 230px,#fbfbfa,rgba(251,251,250,0) 70%),radial-gradient(ellipse 90px 160px at 390px 260px,#f6f5f2,rgba(246,245,242,0) 70%),radial-gradient(ellipse 240px 50px at 240px 370px,#e9e5df,rgba(233,229,223,0) 70%),linear-gradient(180deg,#f4f2ef 0%,#e6ddd1 30%,#b89c78 60%,#d8cfc3)"></div>
</section>

<footer class="footer">
  <div class="brand">Veltaro</div>
  <div class="brand-sub">CANADA</div>
  <div class="f-contact" style="top:152px"><svg width="12" height="16" viewBox="0 0 12 16"><path d="M6 0a6 6 0 0 0-6 6c0 4.5 6 10 6 10s6-5.5 6-10a6 6 0 0 0-6-6zm0 8.5A2.5 2.5 0 1 1 6 3.5a2.5 2.5 0 0 1 0 5z" fill="#fff"/></svg><div><b>Veltaro Canada</b><br>1180 Harbour Lane West,<br>Kingsport, ON L4B 2K7</div></div>
  <div class="f-contact" style="top:222px"><svg width="14" height="14" viewBox="0 0 24 24"><path d="M6.6 10.8a15 15 0 0 0 6.6 6.6l2.2-2.2a1 1 0 0 1 1-.25 11.4 11.4 0 0 0 3.6.6 1 1 0 0 1 1 1V20a1 1 0 0 1-1 1A17 17 0 0 1 3 4a1 1 0 0 1 1-1h3.5a1 1 0 0 1 1 1c0 1.25.2 2.45.6 3.6a1 1 0 0 1-.25 1z" fill="#fff"/></svg><div><b>Sales :</b> 905-555-0140</div></div>
  <div class="f-contact" style="top:254px"><svg width="14" height="14" viewBox="0 0 24 24"><path d="M6.6 10.8a15 15 0 0 0 6.6 6.6l2.2-2.2a1 1 0 0 1 1-.25 11.4 11.4 0 0 0 3.6.6 1 1 0 0 1 1 1V20a1 1 0 0 1-1 1A17 17 0 0 1 3 4a1 1 0 0 1 1-1h3.5a1 1 0 0 1 1 1c0 1.25.2 2.45.6 3.6a1 1 0 0 1-.25 1z" fill="#fff"/></svg><div><b>Parts &amp; Services :</b> 888-555-0175</div></div>
  <div class="f-contact" style="top:286px"><svg width="14" height="14" viewBox="0 0 24 24"><path d="M6.6 10.8a15 15 0 0 0 6.6 6.6l2.2-2.2a1 1 0 0 1 1-.25 11.4 11.4 0 0 0 3.6.6 1 1 0 0 1 1 1V20a1 1 0 0 1-1 1A17 17 0 0 1 3 4a1 1 0 0 1 1-1h3.5a1 1 0 0 1 1 1c0 1.25.2 2.45.6 3.6a1 1 0 0 1-.25 1z" fill="#fff"/></svg><div><b>Main Line :</b> 888-555-0123</div></div>

  <div class="f-head" style="left:450px">Quick Links</div>
  <div class="f-links" style="left:450px">• Home<br>• Tanning<br>• Massage<br>• Red Light<br>• Salon Startup<br>• About Us<br>• Contact Us</div>
  <div class="f-links" style="left:597px">• Privacy Policy<br>• Customer Service<br>• Blog<br>• Terms of Service</div>

  <div class="f-head" style="left:827px">Stay Connected</div>
  <div class="socials"><span></span><span></span><span></span><span></span><span></span><span></span></div>
  <div class="search">Let us help you find what you need<svg width="16" height="16" viewBox="0 0 24 24" fill="none" stroke="#6f7cc4" stroke-width="2.4"><circle cx="10" cy="10" r="6"/><path d="M15 15l6 6"/></svg></div>

  <p class="disclaimer">Tanning 510(k) K204417 • Contraindication: This Product Is Contraindicated For Use On Persons Under The Age Of 18 Years. *Contraindication: This Product Must Not Be Used If Skin Lesions Or Open Wounds Are Present.* *Warning: This Product Should Not Be Used On Individuals Who Have Had Skin Cancer Or Have A Family History Of Skin Cancer.* *Warning: Persons Repeatedly Exposed To UV Radiation Should Be Regularly Evaluated For Skin Cancer.<br><span style="display:block;margin-top:10px">*Veltaro reserves the right to change design and specifications without notice.</span></p>
</footer>
<div class="copyright">© 2023 Veltaro Canada. All Rights Reserved.</div>

</body>
</html>
```